Website for IT consulting Company

I need a website upgrade, the existing site content is ok, I would also like to add a testimonial page, the site should be something that is easy for us to update content. You use the content from www.kelvanbrook.com as an example. I will also post update logo and artwork. I also need a contact form with some type of validation or captcha.

I added Coded to the Project

Please omit Address maps

Target Market(s)

small business, service oriented companies. We provide IT Consulting, support and mangement

Industry/Entity Type

Information Technology

Coding

Number of Pages Required

1 page

Font styles to use
Serif
Sans Serif

Requirements
Must have
• Contain logo attached, and content from existing web site www.kelvanbrook.com.
• Also need to update content easily, and be movable to different platforms.
• There is a catch phrase
• "Let us worry about your technology…” “ so you don’t have to!”
• Should be included.
Nice to have
• Testimonial page, Project page where we can post new and past projects and pictures
Should not have
• none

```html
<!DOCTYPE html>
<html lang="en">
<head>
<meta charset="utf-8">
<title>Kelvanbrook Development Group – IT Consulting</title>
<link href="https://fonts.googleapis.com/css2?family=Roboto:wght@400;500;700&family=Kalam:wght@400&display=swap" rel="stylesheet">
<style>
:root{
  --blue:#3a92dc;
  --blue-dark:#1f76cc;
  --blue-light:#4aa3e6;
  --accent:#2b7fd0;
  --ink:#222;
  --text:#333;
  --muted:#555;
  --soft:#f2f4f7;
  --line:#7fb3e2;
  --white:#fff;
  --orange:#f08a24;
}
*{box-sizing:border-box;margin:0;padding:0}
html,body{width:699px;height:1200px;overflow:hidden}
body{position:relative;font-family:"Roboto",Arial,sans-serif;color:var(--text);background:var(--white)}
.abs{position:absolute}
.hero{left:0;top:0;width:699px;height:326px;background:linear-gradient(160deg,#6b7f94 0%,#4f6478 45%,#3b4d60 100%)}
.topbar{left:0;top:0;width:699px;height:40px;background:var(--blue);opacity:.92}
.logo{left:29px;top:0;width:128px;height:45px;background:var(--white);border-radius:0 0 3px 3px;display:flex;align-items:center;justify-content:center;gap:5px;box-shadow:0 1px 4px rgba(0,0,0,.2)}
.logo .mark{width:10px;height:10px;background:var(--orange)}
.logo span{font-weight:700;font-size:12px;color:var(--orange);letter-spacing:.3px}
.nav{right:10px;top:14px;display:flex;gap:22px;font-size:8.5px;color:var(--white);letter-spacing:.2px}
.tagline{left:0;width:699px;text-align:center;font-family:"Kalam",cursive;color:var(--white);font-size:17px}
.btn-ghost{left:310px;top:206px;width:77px;height:23px;border:1px solid rgba(255,255,255,.8);border-radius:3px;color:var(--white);font-size:8.5px;display:flex;align-items:center;justify-content:center}
.infobar{left:0;top:326px;width:699px;height:19px;background:#eef0f3;border-bottom:1px solid #ddd;font-size:7.5px;color:#777;display:flex;align-items:center}
.infobar .item{display:flex;align-items:center;gap:4px;margin-left:30px}
.infobar .item+.item{margin-left:16px}
.infobar .social{margin-left:auto;margin-right:30px;display:flex;gap:12px;align-items:center}
.sq{width:10px;height:10px;background:#8a9db3;border-radius:2px}
.section-title{left:0;width:699px;text-align:center;font-size:13px;font-weight:500;color:var(--ink)}
.section-title b{color:var(--accent);font-weight:500}
.dots{left:30px;width:639px;border-top:1px dashed var(--line)}
.intro{left:34px;top:385px;width:631px;text-align:center;font-size:6.8px;line-height:11.5px;color:var(--text)}
.solutions{left:0;top:428px;width:699px;height:169px;background:var(--soft)}
.service{width:100px;text-align:center;top:471px}
.service .pic{width:82px;height:82px;border-radius:50%;margin:0 auto;background:linear-gradient(135deg,#7e8fa3,#3e5168)}
.service h3{font-size:10px;font-weight:500;color:var(--ink);line-height:13px;margin-top:11px}
.panel{top:597px;width:233px;height:132px;background:var(--blue);color:var(--white);text-align:center;padding:14px 14px 0}
.panel.mid{background:var(--blue-dark)}
.panel h2{font-size:14.5px;font-weight:500;line-height:15px;margin-bottom:9px}
.panel p{font-size:7.8px;line-height:13px}
.testimonials{left:0;top:729px;width:699px;height:196px;background:var(--soft)}
.quote{width:236px;font-size:6.9px;line-height:11.5px;color:#555}
.quote i{display:block}
.quote .who{font-style:normal;color:var(--ink);font-size:7px;margin-top:6px}
.quote.r{text-align:right}
.avatar{width:45px;height:45px;border-radius:50%;background:linear-gradient(135deg,#b9a89a,#5b4a40)}
.vline{left:349px;top:785px;height:128px;border-left:1px dashed var(--line)}
.hline{left:30px;top:847px;width:639px;border-top:1px dashed var(--line)}
.likebar{left:37px;top:946px;width:624px;border-top:1px solid #e3e3e3}
.likebox{left:218px;top:932px;width:262px;height:27px;background:var(--white);border:1px solid #e0e0e0;border-radius:14px;display:flex;align-items:center}
.likebox .thumb{width:34px;height:100%;border-right:1px solid #e0e0e0;display:flex;align-items:center;justify-content:center}
.likebox .pill{margin-left:36px;background:var(--blue-dark);color:var(--white);font-size:6px;font-weight:700;padding:2px 4px;border-radius:2px;display:flex;gap:2px;align-items:center}
.likebox .txt{font-size:5.8px;color:#333;margin-left:4px}
.footer{left:0;top:968px;width:699px;height:232px;background:linear-gradient(180deg,#3c93dd,#2f86d6);color:var(--white)}
.footer h4{font-size:10.5px;font-weight:500}
.fcol{font-size:7px;line-height:11.5px}
.field{background:var(--white);border:1px solid #cfe0ef;border-radius:2px;height:18px;font-size:7px;color:#888;padding:4px 8px}
.send{left:310px;top:1117px;width:79px;height:19px;background:var(--white);color:#222;font-size:7.2px;border-radius:2px;display:flex;align-items:center;justify-content:center}
.ficons{display:flex;gap:9px;margin-top:8px}
.ficons i{width:8px;height:8px;border-radius:50%;background:rgba(255,255,255,.85);display:block}
.fline{left:30px;top:1162px;width:639px;border-top:1px solid rgba(255,255,255,.6)}
.copy{top:1178px;font-size:6.8px;font-weight:500}
.flogo{left:304px;top:1174px;display:flex;gap:4px;align-items:center}
.flogo .mark{width:8px;height:8px;background:var(--orange)}
.flogo span{font-size:9px;font-weight:700;color:var(--orange)}
</style>
</head>
<body>

<header>
  <div class="abs hero" role="img" aria-label="Photo of hands working on a tablet showing charts, with a coffee cup"></div>
  <div class="abs topbar"></div>
  <div class="abs logo"><i class="mark"></i><span>KELVANBROOK</span></div>
  <nav class="abs nav"><span>HOME</span><span>ABOUT</span><span>SUPPORT</span><span>CLIENTS</span><span>PROJECT</span><span>CAREERS</span><span>CONTACT</span></nav>
  <p class="abs tagline" style="top:143px">Let us worry about your technology…</p>
  <p class="abs tagline" style="top:170px">so you don't have to</p>
  <div class="abs btn-ghost">Learn More</div>
</header>

<div class="abs infobar">
  <span class="item"><svg width="8" height="8" viewBox="0 0 24 24"><path fill="#888" d="M6.6 10.8a15 15 0 0 0 6.6 6.6l2.2-2.2c.3-.3.7-.4 1-.2 1.1.4 2.3.6 3.6.6.6 0 1 .4 1 1V20c0 .6-.4 1-1 1A17 17 0 0 1 3 4c0-.6.4-1 1-1h3.5c.6 0 1 .4 1 1 0 1.3.2 2.5.6 3.6.1.3 0 .7-.2 1z"/></svg>+1 800 555 01 42</span>
  <span class="item"><svg width="9" height="7" viewBox="0 0 24 18"><rect width="24" height="18" rx="2" fill="#888"/><path d="M1 1l11 9 11-9" stroke="#eef0f3" stroke-width="2" fill="none"/></svg>info@yourdomain.com</span>
  <span class="social"><i class="sq"></i><i class="sq"></i><i class="sq"></i>
    <svg width="9" height="9" viewBox="0 0 24 24"><circle cx="10" cy="10" r="6.5" stroke="#888" stroke-width="3" fill="none"/><path d="M15 15l7 7" stroke="#888" stroke-width="3"/></svg></span>
</div>

<section>
  <h1 class="abs section-title" style="top:350px">Welcome to <b>Kelvanbrook Development Group, Inc</b></h1>
  <div class="abs dots" style="top:373px"></div>
  <p class="abs intro">Kelvanbrook is a technology solution provider based in Houston, Texas. Our goal is to make technology a non-issue for individuals and small to medium size businesses ranging from 5 to 150 Users. Kelvanbrook has the experience, the tools, high-level technology solutions and training to power your business and your work force. We understand that all business's have one goal in common! (KDG) A Return on Investment</p>
</section>

<section>
  <div class="abs solutions"></div>
  <h2 class="abs section-title" style="top:434px">IT Support <b>Solutions</b></h2>
  <div class="abs dots" style="top:457px"></div>
  <div class="abs service" style="left:27px"><div class="pic" role="img" aria-label="Technician working at a server rack"></div><h3>Network<br>Administration</h3></div>
  <div class="abs service" style="left:134px"><div class="pic" role="img" aria-label="Blue network patch cables" style="background:linear-gradient(135deg,#3a78c8,#15356b)"></div><h3>Network<br>Cabling</h3></div>
  <div class="abs service" style="left:241px"><div class="pic" role="img" aria-label="Team meeting around a laptop" style="background:linear-gradient(135deg,#b49a82,#4a3a2e)"></div><h3>Network<br>Security</h3></div>
  <div class="abs service" style="left:348px"><div class="pic" role="img" aria-label="Hand using a wireless router" style="background:linear-gradient(135deg,#d7d7d7,#3a3a3a)"></div><h3>Wireless<br>Networks</h3></div>
  <div class="abs service" style="left:455px"><div class="pic" role="img" aria-label="Man in glasses at an office desk" style="background:linear-gradient(135deg,#e3e6ea,#8a8f96)"></div><h3>Antivirus<br>Solutions</h3></div>
  <div class="abs service" style="left:562px"><div class="pic" role="img" aria-label="Support staff at a desktop computer" style="background:linear-gradient(135deg,#c9c2b6,#544b42)"></div><h3>Desktop<br>Support</h3></div>
</section>

<section>
  <div class="abs panel" style="left:0"><h2>IT Infrastructure Design and Installation</h2><p>Our staff will design, service, administer and maintain your IT needs.<br>We are well versed on all major operating system, and network appliances</p></div>
  <div class="abs panel mid" style="left:233px;width:233px"><h2>Managed IT Solutions</h2><p>Do you need a quick solution to a technical problem? With our live remote-assistance tool, a member of our support team can view your desktop and share control of your mouse and keyboard to get you on your way to a solution.</p></div>
  <div class="abs panel" style="left:466px"><h2>Remote Diagnostic and Support</h2><p>Do you have more than one site? Do you need remote access? We can design and implement LANS/WANS and VPN's. Make your important data available to you wherever you are.</p></div>
</section>

<section>
  <div class="abs testimonials"></div>
  <h2 class="abs section-title" style="top:734px">What <b>People Say</b></h2>
  <div class="abs dots" style="top:757px"></div>
  <div class="abs vline"></div>
  <div class="abs hline"></div>

  <div class="abs quote r" style="left:33px;top:783px"><i>Duis aute irure dolor in reprehenderit in voluptate velit esse cillum dolore eu fugiat nulla pariatur. Excepteur sint occaecat cupidatat non proident, sunt in culpa qui officia deserunt mollit.</i><p class="who">Evan Morrow, Operations Manager</p></div>
  <div class="abs avatar" style="left:285px;top:784px" role="img" aria-label="Portrait of client"></div>
  <div class="abs avatar" style="left:368px;top:784px" role="img" aria-label="Portrait of client"></div>
  <div class="abs quote" style="left:430px;top:783px"><i>Provident, similique sunt in culpa qui officia deserunt mollitia animi, id est laborum et dolorum fuga. Et harum quidem rerum facilis est et expedita distinctio. Nam libero tempore, cum soluta nobis.</i><p class="who">Nora Whitfield, Creative Designer</p></div>

  <div class="abs quote r" style="left:33px;top:863px"><i>Luis aute irure dolor in reprehenderit in piluptate velit esse cillum dolore eu fugiat nulla pariatur. Excepteur sint occaecat cupidatat non proident, sunt in culpa qui officia deserunt mollit.</i><p class="who">Clara Boone, Manager</p></div>
  <div class="abs avatar" style="left:285px;top:864px" role="img" aria-label="Portrait of client"></div>
  <div class="abs avatar" style="left:368px;top:864px" role="img" aria-label="Portrait of client"></div>
  <div class="abs quote" style="left:430px;top:863px"><i>At vero eos et accusamus et iusto odio dignissimos ducimus qui blanditiis praesentium voluptatum deleniti atque corrupti quos dolores et quas molestias excepturi sint occaecati asperiores.</i><p class="who">Ray Ostrand, Developer</p></div>
</section>

<div class="abs likebar"></div>
<div class="abs likebox">
  <span class="thumb"><svg width="11" height="11" viewBox="0 0 24 24"><path d="M2 10h4v11H2zM8 21V10l5-8c1.5 0 2.5 1 2 3l-1 4h6c1.2 0 2 1 1.8 2l-1.6 8c-.2.8-.9 2-1.9 2z" fill="none" stroke="#bbb" stroke-width="1.6"/></svg></span>
  <span class="pill"><svg width="6" height="6" viewBox="0 0 10 10"><path d="M1 5l3 3 5-6" stroke="#fff" stroke-width="2" fill="none"/></svg>Like</span>
  <span class="txt">You and 4k others like this.</span>
</div>

<footer>
  <div class="abs footer"></div>
  <div class="abs fcol" style="left:30px;top:983px;width:150px">
    <h4 style="margin-bottom:10px">Contact Us</h4>
    <p>Please feel free to contact us for any issue. Our staff is available to you from 9AM until 5PM on weekdays.</p>
    <p style="margin-top:8px"><b>Phone:</b> +1 (555) 014-2287</p>
    <p style="margin-top:8px"><b>Office:</b> 418 Marlow Ave. Houston, TX 77019</p>
    <p style="margin-top:8px"><b>Email:</b> info@kelvanbrook.com</p>
    <div class="ficons"><i></i><i></i><i></i><i></i><i></i></div>
  </div>

  <h4 class="abs" style="left:194px;top:983px;width:311px;text-align:center;color:var(--white);font-size:10.5px;font-weight:500">Feel Free to Mail</h4>
  <div class="abs field" style="left:194px;top:1009px;width:150px">Name *</div>
  <div class="abs field" style="left:355px;top:1009px;width:150px">Email *</div>
  <div class="abs field" style="left:194px;top:1039px;width:311px">Subject</div>
  <div class="abs field" style="left:194px;top:1069px;width:311px;height:38px">Write Your Message Here...</div>
  <div class="abs send">SEND MESSAGE</div>

  <div class="abs fcol" style="left:521px;top:983px;width:150px">
    <h4 style="margin-bottom:10px">About Team</h4>
    <p>Enim congue blandit. Lorem ipsum dolor sit amet, consectetur adipiscing elit. Quisque consectetur interdum finibus. Vestibulum ante ipsum primis in faucibus orci. luctus et ultrices posuere.</p>
    <p style="margin-top:8px">Cubilia cras blandit finibus ipsum, id porttitor arcu volutpat a. Integer iaculis erat nec justo malesuada faucibus vel tempus sapien. Vivamus aliquam euismod tristique.</p>
  </div>

  <div class="abs fline"></div>
  <p class="abs copy" style="left:30px;color:var(--white)">Copyright © Kelvanbrook Development Group, Inc.</p>
  <div class="abs flogo"><i class="mark"></i><span>KELVANBROOK</span></div>
  <p class="abs copy" style="right:30px;color:var(--white)">All rights reserved</p>
</footer>

</body>
</html>
```